Kelvaro.ch is looking for business card letterhead and envelope C5 with WOW effect

We need a strong business card for our company Kelvaro.ch, logo is available. You want a black or dark background on which the logo Stark r% 26 # 252; appears. Letterhead and envelope in C5 format should be in a similar design, but does not have to be We need a strong business card for our company Kelvaro.ch, logo is available. A black or dark background is desired, on which the logo Stark comes across. The letterhead and the envelope in C5 format should have a similar design.

Target Market(s)

Private customers as well as entrepreneurs

Contact Information for Business Card

E-mail: info@kelvaro-example.ch
Web.www.Kelvaro-example.ch
Tel: +41 ( 0 ) 79 482 6037
Adresse:
Lindenweg 14
9406 Tarnbach

Hier kann man Icons verwenden für Email,Tel und Adressse

Font styles to use
Other font styles liked:
• Dubai,bold

Colors

Designer to choose colors to be used in the design.

Requirements
Must have
• WOW effect
Nice to have
• R% 26 # 252; back business card with our service listings. - VEHICLE LABELING - SHOP WINDOW LABELING - STICKERS AND MUCH MORE ... in red color

```html
<!DOCTYPE html>
<html lang="en">
<head>
<meta charset="utf-8">
<title>Kelvaro.ch – Business Card</title>
<link rel="stylesheet" href="https://fonts.googleapis.com/css2?family=Ubuntu:wght@400;500;700&family=Black+Ops+One&display=swap">
<style>
  :root {
    --ink: #0b0b0b;
    --ink-soft: #1a1a1a;
    --stage: #2a2a2a;
    --yellow: #fdc91c;
    --white: #ffffff;
  }
  * { margin: 0; padding: 0; box-sizing: border-box; }
  html, body { width: 1200px; height: 900px; overflow: hidden; }
  body {
    background: var(--stage);
    font-family: "Ubuntu", sans-serif;
    position: relative;
  }
  .card {
    position: absolute;
    left: 250px;
    width: 700px;
    height: 400px;
    background: var(--ink);
    overflow: hidden;
  }
  .card--front { top: 40px; border-right: 4px solid var(--yellow); }
  .card--back { top: 460px; border-left: 4px solid var(--yellow); }

  /* Front */
  .front-pattern {
    position: absolute;
    left: 0; top: 0;
    width: 330px; height: 400px;
    background: radial-gradient(ellipse at 45% 55%, rgba(253,201,28,0.85) 0%, rgba(253,201,28,0.35) 45%, rgba(11,11,11,0) 75%);
  }
  .front-shade {
    position: absolute;
    right: 0; top: 0;
    width: 330px; height: 400px;
    background: radial-gradient(ellipse at 60% 50%, var(--ink-soft) 0%, rgba(11,11,11,0) 70%);
  }
  .front-wordmark {
    position: absolute;
    left: 340px; top: 165px;
    font-family: "Ubuntu", sans-serif;
    font-weight: 700;
    font-size: 56px;
    letter-spacing: 1px;
    color: var(--white);
  }

  /* Back */
  .band-top {
    position: absolute;
    left: 0; top: 0;
    width: 100%; height: 125px;
    background: var(--yellow);
  }
  .band-logo {
    position: absolute;
    left: 440px; top: 125px;
    width: 260px; height: 70px;
    background: var(--yellow);
  }
  .rule-left {
    position: absolute;
    left: 0; top: 131px;
    width: 420px; height: 2px;
    background: var(--yellow);
  }
  .rule-right {
    position: absolute;
    left: 420px; top: 201px;
    width: 280px; height: 2px;
    background: var(--yellow);
  }
  .back-logo {
    position: absolute;
    left: 455px; top: 110px;
    display: flex; align-items: center; gap: 10px;
  }
  .back-logo__mark {
    width: 22px; height: 22px;
    background: var(--white);
  }
  .back-logo__name {
    font-weight: 700;
    font-size: 30px;
    color: var(--ink);
  }
  .contact {
    position: absolute;
    left: 430px; top: 212px;
    width: 260px;
    color: var(--white);
  }
  .contact__name {
    font-family: "Black Ops One", sans-serif;
    font-size: 25px;
    color: var(--yellow);
    letter-spacing: 1px;
    line-height: 1;
  }
  .contact__role { font-size: 14px; margin-top: 3px; }
  .contact__list { list-style: none; margin-top: 12px; }
  .contact__list li {
    display: flex; align-items: center; gap: 8px;
    font-size: 14px; height: 21px;
  }
  .contact__list svg { width: 14px; height: 14px; flex: none; }
  .highlight { color: var(--yellow); font-weight: 700; }
  .contact__rule {
    height: 2px; width: 220px;
    background: var(--yellow);
    margin: 10px 0 10px;
  }
  .contact__address {
    display: flex; align-items: center; gap: 8px;
    font-size: 14px;
  }
  .contact__address svg { width: 15px; height: 15px; flex: none; }
</style>
</head>
<body>
  <section class="card card--front">
    <div class="front-pattern" role="img" aria-label="Decorative yellow geometric pattern area"></div>
    <div class="front-shade"></div>
    <div class="front-wordmark">KELVARO.CH</div>
  </section>

  <section class="card card--back">
    <div class="band-top"></div>
    <div class="band-logo"></div>
    <div class="rule-left"></div>
    <div class="rule-right"></div>
    <div class="back-logo">
      <span class="back-logo__mark"></span>
      <span class="back-logo__name">KELVARO.CH</span>
    </div>

    <div class="contact">
      <div class="contact__name">MAREK TOLSEN</div>
      <div class="contact__role">Owner/ CEO</div>
      <ul class="contact__list">
        <li>
          <svg viewBox="0 0 16 16" fill="none" stroke="#fdc91c" stroke-width="1.5"><path d="M4 2l2.5 3-1.5 1.5c.8 1.8 2.2 3.2 4 4L10.5 9l3 2.5-1.5 2c-5 0-10-5-10-10z"/></svg>
          +41 ( 0 ) 79 482 6037
        </li>
        <li>
          <svg viewBox="0 0 16 16" fill="none" stroke="#fdc91c" stroke-width="1.5"><rect x="1.5" y="3.5" width="13" height="9"/><path d="M1.5 3.5L8 9l6.5-5.5"/></svg>
          info@kelvaro-example.ch
        </li>
        <li>
          <svg viewBox="0 0 16 16" fill="none" stroke="#fdc91c" stroke-width="1.4"><circle cx="8" cy="8" r="6.5"/><ellipse cx="8" cy="8" rx="3" ry="6.5"/><path d="M1.5 8h13M2.5 4.8h11M2.5 11.2h11"/></svg>
          <span>www.<span class="highlight">Kelvaro-example</span>.ch</span>
        </li>
      </ul>
      <div class="contact__rule"></div>
      <div class="contact__address">
        <svg viewBox="0 0 16 16" fill="none" stroke="#fdc91c" stroke-width="1.5"><path d="M2 8L8 2.5 14 8M3.5 7v7h9V7"/><rect x="6.5" y="10" width="3" height="4"/></svg>
        Lindenweg 14, 9406 Tarnbach
      </div>
    </div>
  </section>
</body>
</html>
```